TA BRAMLEY BUSINESS CARD DESIGN PROJECT

We need to utilize our logo that was expertly created on PixelHarbor and now need to match this with a business card design.

```html
<!DOCTYPE html>
<html lang="en">
<head>
<meta charset="utf-8">
<title>TA Bramley Business Cards</title>
<link rel="stylesheet" href="https://fonts.googleapis.com/css2?family=Montserrat:wght@400;700&display=swap">
<style>
  :root {
    --stage: #3b3b3d;
    --card-dark: #151515;
    --emboss: #2b2b2b;
    --card-light: #ffffff;
    --brand-blue: #1257a8;
    --ink: #333333;
  }
  * { margin: 0; padding: 0; box-sizing: border-box; }
  html, body { width: 1200px; height: 689px; overflow: hidden; }
  body {
    background: var(--stage);
    font-family: "Montserrat", Arial, sans-serif;
    position: relative;
  }
  .card {
    position: absolute;
    top: 190px;
    width: 540px;
    height: 309px;
    border-radius: 22px;
    overflow: hidden;
  }
  .card-front { left: 40px; background: var(--card-dark); }
  .card-back { left: 620px; background: var(--card-light); }

  .front-name {
    position: absolute;
    inset: 0;
    display: flex;
    align-items: center;
    justify-content: center;
    font-weight: 700;
    font-size: 54px;
    letter-spacing: 6px;
    color: var(--emboss);
  }

  .swoosh { position: absolute; inset: 0; width: 100%; height: 100%; }

  .back-name {
    position: absolute;
    right: 36px;
    top: 56px;
    font-weight: 700;
    font-size: 34px;
    letter-spacing: 4px;
    color: var(--brand-blue);
  }
  .person {
    position: absolute;
    left: 40px;
    top: 166px;
  }
  .person-name {
    font-weight: 700;
    font-size: 17px;
    color: var(--brand-blue);
    letter-spacing: 0.5px;
  }
  .person-role { font-size: 12px; color: var(--ink); }
  .divider {
    position: absolute;
    left: 36px;
    right: 24px;
    top: 216px;
    height: 1.5px;
    background: var(--brand-blue);
  }
  .contacts {
    position: absolute;
    left: 44px;
    top: 228px;
    list-style: none;
    font-size: 13px;
    line-height: 1.55;
    color: var(--ink);
  }
  .contacts li { display: flex; align-items: center; gap: 7px; }
  .contacts svg { width: 11px; height: 11px; fill: var(--brand-blue); flex: none; }
  .address {
    position: absolute;
    right: 30px;
    top: 236px;
    text-align: right;
    font-size: 12px;
    line-height: 1.35;
    color: var(--ink);
  }
</style>
</head>
<body>
  <section class="card card-front">
    <div class="front-name">TA BRAMLEY</div>
  </section>

  <section class="card card-back">
    <svg class="swoosh" viewBox="0 0 540 309" aria-hidden="true">
      <path d="M0 0 H330 C190 45 70 95 0 165 Z" fill="var(--brand-blue)"/>
      <path d="M346 0 C205 50 80 110 0 190" fill="none" stroke="var(--brand-blue)" stroke-width="3"/>
    </svg>

    <div class="back-name">TA BRAMLEY</div>

    <div class="person">
      <div class="person-name">MARCUS HALE</div>
      <div class="person-role">Managing Director</div>
    </div>

    <div class="divider"></div>

    <ul class="contacts">
      <li>
        <svg viewBox="0 0 24 24" aria-hidden="true"><path d="M6.6 10.8a15.1 15.1 0 0 0 6.6 6.6l2.2-2.2c.3-.3.7-.4 1-.2 1.1.4 2.3.6 3.6.6.6 0 1 .4 1 1V20c0 .6-.4 1-1 1A17 17 0 0 1 3 4c0-.6.4-1 1-1h3.5c.6 0 1 .4 1 1 0 1.3.2 2.5.6 3.6.1.3 0 .7-.2 1z"/></svg>
        123 456 789
      </li>
      <li>
        <svg viewBox="0 0 24 24" aria-hidden="true"><path d="M2 5h20v14H2z"/></svg>
        info@yourgmail.com
      </li>
      <li>
        <svg viewBox="0 0 24 24" aria-hidden="true"><circle cx="12" cy="12" r="10"/></svg>
        www.yourwebsite.com
      </li>
    </ul>

    <div class="address">Your address, City<br>State, Zip 1234</div>
  </section>
</body>
</html>
```